Business card for Luxury Portable Restroom Trailer company

We are a Luxury Portable Restroom Trailer Company Called FALCRIDGE HIRES. Based in Orange County California. We provide portable restroom trailers for events, such as, Weddings, Concerts, Charity events, Sporting events, Tournaments, Corporate events, ect. We rent and Sell the Luxury restrooms. Our colors are white, grey, and Orange. As you will see in the logo we uploaded.
There are 2 people in the company so the names and titles will change for the 3 people but card will remain the same. Here is the information for each Person: Dwight Penner CFO 555 318-0476
next Person: Leon Marchetti VP 555 318-0476
Next Person: Owen Marchetti CEO 555 318-0476
Information to include on the card: Luxury Restroom Trailers Rental and Sales. Weddings, Concerts, Charity, Sporting and Corp. Events.

```html
<!DOCTYPE html>
<html lang="en">
<head>
<meta charset="utf-8">
<title>Falcridge Hires – Business Card</title>
<link href="https://fonts.googleapis.com/css2?family=Figtree:wght@400;500;700;800&display=swap" rel="stylesheet">
<style>
  :root {
    --orange: #f26c26;
    --grey: #58585a;
    --ink: #1d1d1f;
    --white: #ffffff;
    --backdrop: #e4e6e6;
  }
  * { box-sizing: border-box; margin: 0; padding: 0; }
  html, body {
    width: 1179px; height: 1200px; overflow: hidden;
    background: var(--backdrop);
    font-family: "Figtree", "Helvetica Neue", Arial, sans-serif;
  }
  .card {
    position: absolute; left: 220px;
    width: 738px; height: 424px;
    background: var(--white);
    overflow: hidden;
  }
  .card-front { top: 161px; }
  .card-back { top: 618px; }

  /* front */
  .brand-band {
    position: absolute; top: 0; right: 0;
    width: 232px; height: 100%;
    background: var(--orange);
  }
  .brand-disc { position: absolute; left: 370px; top: 53px; width: 328px; height: 328px; }
  .wordmark {
    color: var(--grey); font-weight: 800; letter-spacing: 1px;
    line-height: 1; white-space: nowrap;
  }
  .card-front .wordmark { position: absolute; left: 36px; top: 50px; font-size: 30px; }
  .team { position: absolute; left: 36px; top: 126px; }
  .member { margin-bottom: 8px; }
  .member-name {
    color: var(--orange); font-weight: 700; font-size: 24px;
    line-height: 28px; letter-spacing: 0.2px;
  }
  .member-role, .member-phone {
    color: var(--ink); font-weight: 400; font-size: 19px; line-height: 26px;
  }
  .member-phone { display: flex; align-items: center; gap: 9px; }
  .member-phone svg { width: 18px; height: 14px; flex: none; }

  /* back */
  .card-back .wordmark {
    position: absolute; left: 0; right: 0; top: 150px;
    text-align: center; font-size: 56px; letter-spacing: 2px;
  }
  .services {
    position: absolute; left: 0; right: 0; top: 318px;
    text-align: center; color: var(--ink);
    font-size: 19px; line-height: 27px;
  }
  .services li { display: inline; list-style: none; margin: 0 6px; }
  .services li::before {
    content: ""; display: inline-block; width: 11px; height: 11px;
    border-radius: 50%; background: var(--orange);
    margin-right: 9px; vertical-align: 1px;
  }
</style>
</head>
<body>

<section class="card card-front">
  <div class="brand-band"></div>
  <svg class="brand-disc" viewBox="0 0 328 328" role="img" aria-label="Brand emblem circle">
    <circle cx="164" cy="164" r="164" fill="var(--white)"/>
    <circle cx="164" cy="164" r="144" fill="none" stroke="var(--orange)" stroke-width="16"/>
  </svg>

  <div class="wordmark">FALCRIDGE HIRES</div>

  <div class="team">
    <div class="member">
      <div class="member-name">DWIGHT PENNER</div>
      <div class="member-role">CFO</div>
      <div class="member-phone">
        <svg viewBox="0 0 18 14"><path d="M1 5c0-3 4-4 8-4s8 1 8 4l-3 1-1-2H5L4 6z" fill="var(--orange)"/><rect x="3" y="7" width="12" height="7" rx="1" fill="var(--orange)"/></svg>
        555 318-0476
      </div>
    </div>
    <div class="member">
      <div class="member-name">LEON MARCHETTI</div>
      <div class="member-role">VP</div>
      <div class="member-phone">
        <svg viewBox="0 0 18 14"><path d="M1 5c0-3 4-4 8-4s8 1 8 4l-3 1-1-2H5L4 6z" fill="var(--orange)"/><rect x="3" y="7" width="12" height="7" rx="1" fill="var(--orange)"/></svg>
        555 318-0476
      </div>
    </div>
    <div class="member">
      <div class="member-name">OWEN MARCHETTI</div>
      <div class="member-role">CEO</div>
      <div class="member-phone">
        <svg viewBox="0 0 18 14"><path d="M1 5c0-3 4-4 8-4s8 1 8 4l-3 1-1-2H5L4 6z" fill="var(--orange)"/><rect x="3" y="7" width="12" height="7" rx="1" fill="var(--orange)"/></svg>
        555 318-0476
      </div>
    </div>
  </div>
</section>

<section class="card card-back">
  <div class="wordmark">FALCRIDGE HIRES</div>
  <ul class="services">
    <li>Luxury Restroom Trailers Rental and Sales</li><br>
    <li>Weddings</li><li>Concerts</li><li>Charity</li><li>Sporting and Corp</li><li>Events</li>
  </ul>
</section>

</body>
</html>
```